Electrician Letterhead Design MVR

We need some letterhead for our bills and other papers.
Customer address is on the right side (Swiss format)
A4 format

Design should also be applicable on Cards

Target Market(s)

Private Customers, Small Business

Industry/Entity Type

Electrician

Other font styles liked:
• incised 901

Colors
00AB8E
00BBA5
67D7C9
C6EFE9
E9F9F6

```html
<!DOCTYPE html>
<html lang="en">
<head>
<meta charset="utf-8">
<title>MVR Letterhead</title>
<link rel="stylesheet" href="https://fonts.googleapis.com/css2?family=Arimo:wght@400;700&family=Questrial&display=swap">
<style>
  :root {
    --teal: #009a86;
    --ink: #111111;
    --text: #555555;
    --page: #ffffff;
    --backdrop: #dcdcdc;
  }
  * { margin: 0; padding: 0; box-sizing: border-box; }
  html, body { width: 1189px; height: 1200px; overflow: hidden; background: var(--backdrop); }
  .letterhead {
    position: absolute; left: 170px; top: 0;
    width: 848px; height: 1200px;
    background: var(--page);
    font-family: "Arimo", Arial, sans-serif;
    color: var(--text);
  }
  .brand-name {
    position: absolute; left: 75px; top: 36px;
    font-family: "Arimo", Arial, sans-serif;
    font-weight: 700; font-size: 92px; line-height: 1;
    color: var(--teal); letter-spacing: 2px;
  }
  .header-band { position: absolute; top: 129px; height: 8px; background: var(--teal); }
  .header-band.left { left: 0; width: 67px; }
  .header-band.right { left: 288px; right: 0; }
  .company-line {
    position: absolute; left: 75px; top: 127px; width: 210px;
    font-family: "Arimo", Arial, sans-serif; font-weight: 700;
    font-size: 11px; line-height: 12px; color: var(--ink); white-space: nowrap;
  }
  .header-rule { position: absolute; left: 0; right: 0; top: 142px; height: 2px; background: var(--ink); }
  .sender-address {
    position: absolute; right: 229px; top: 64px;
    text-align: right; font-size: 14px; line-height: 16.5px; font-style: normal;
  }
  .contact-divider { position: absolute; left: 632px; top: 67px; width: 1px; height: 44px; background: var(--text); }
  .contact-list { position: absolute; left: 649px; top: 64px; list-style: none; font-size: 14px; line-height: 16.5px; }
  .contact-list li { display: flex; align-items: center; gap: 6px; }
  .contact-list svg { width: 9px; height: 9px; flex: none; }
  .salutation {
    position: absolute; left: 77px; top: 364px;
    font-family: "Questrial", sans-serif; font-weight: 400;
    font-size: 20px; color: var(--text); -webkit-text-stroke: 0.4px var(--text);
  }
  .letter-body { position: absolute; left: 77px; top: 420px; width: 700px; }
  .letter-body p { font-size: 13.9px; line-height: 17.5px; margin-bottom: 15px; white-space: nowrap; }
  .closing {
    position: absolute; left: 77px; top: 782px;
    font-family: "Questrial", sans-serif; font-size: 11px; font-weight: 400;
    color: var(--text); -webkit-text-stroke: 0.3px var(--text);
  }
  .signature-area {
    position: absolute; left: 77px; top: 835px; width: 140px; height: 40px;
    background: linear-gradient(90deg, #e2e2e2, #c9c9c9 50%, #e2e2e2);
  }
  .footer-band { position: absolute; left: 0; bottom: 0; width: 848px; height: 17px; }
</style>
</head>
<body>
  <main class="letterhead">
    <header>
      <div class="brand-name">MVR</div>
      <div class="header-band left"></div>
      <div class="company-line">Mivoral Stromwerk Services</div>
      <div class="header-band right"></div>
      <div class="header-rule"></div>

      <address class="sender-address">
        Your address<br>city<br>state, ZIP 0000
      </address>
      <div class="contact-divider"></div>
      <ul class="contact-list">
        <li>
          <svg viewBox="0 0 10 10" aria-hidden="true"><path d="M2 1 L4 3 L3 4 Q4 6 6 7 L7 6 L9 8 L8 9 Q3 9 1 2 Z" fill="var(--teal)"/></svg>
          555-019-4738
        </li>
        <li>
          <svg viewBox="0 0 10 10" aria-hidden="true"><rect x="0.5" y="2" width="9" height="6" fill="var(--teal)"/><path d="M0.5 2 L5 5.5 L9.5 2" stroke="#fff" stroke-width="0.9" fill="none"/></svg>
          youremail@mailbox.com
        </li>
        <li>
          <svg viewBox="0 0 10 10" aria-hidden="true"><circle cx="5" cy="5" r="4.5" fill="var(--teal)"/><path d="M1 5 H9 M5 0.5 V9.5" stroke="#fff" stroke-width="0.8"/></svg>
          www.yourwebsite.com
        </li>
      </ul>
    </header>

    <h1 class="salutation">Dear Mr. Smith,</h1>

    <section class="letter-body">
      <p>Lorem ipsum dolor sit amet, consectetuer adipiscing elit, sed diam nonmmy nibh euismod tincidunt ut laor<br>eet dolore magna aliquam erat volutpat. Ut wisi enim ad minim veniam, quis nostrud exerci tationmcorper<br>suscipit lobortis nisl ut aliquip ex ea commodo consequat. Duis autem vel eum iriure dolor in hendrerit in<br>vulputate velit esse molestie consequat, vel illum dolore eu feugiat</p>
      <p>Rorem ipsum dolor sit amet, consectetuer adipiscing elit, sed diam nonmmy nibh euismod tincidunt ut laor<br>eet dolore magna aliquam erat volutpat. Ut wisi enim ad minim veniam, quis nostrud exerci tationmcorper<br>suscipit lobortis nisl ut aliquip ex ea commodo consequat. Duis autem vel eum iriure dolor in hendrerit in<br>vulputate velit esse molest</p>
      <p>Dorem ipsum dolor sit amet, consectetuer adipiscing elit, sed diam nonmmy nibh euismod tincidunt ut laor<br>eet dolore magna aliquam erat volutpat. Ut wisi enim ad minim veniam, quis nostrud exerci tationmcorper<br>suscipit lobortis nisl ut aliquip ex ea commodo consequat. Duis autem vel eum iriure dolor in hendrerit in<br>suscipit lobortis nisl ut aliquip ex ea commodo consequat. Duis autem vel eum iriure dolor in hendrerit in<br>vulputate velit esse molestie consequat, vel illum</p>
      <p>Sorem ipsum dolor sit amet, consectetuer adipiscing elit, sed diam nonmmy nibh euismod tincidunt ut laor<br>eet dolore magna aliquam erat volutpat. Ut wisi enim ad minim veniam, quis nostrud exerci tationmcorper<br>suscipit lobortis nisl ut aliquip ex ea commodo consequat. Duis autem vel eum iriure dolor in</p>
    </section>

    <div class="closing">Sincerely,</div>
    <div class="signature-area" role="img" aria-label="Handwritten signature of the sender"></div>

    <svg class="footer-band" viewBox="0 0 848 17" aria-hidden="true">
      <polygon points="0,0 627,0 613,17 0,17" fill="var(--teal)"/>
      <polygon points="645,0 848,0 848,17 631,17" fill="var(--ink)"/>
    </svg>
  </main>
</body>
</html>
```